UI/ UX Design for ERP Software

We need a new UX/UI interface for a ERP software for property managers. Our CMMS / ERP solution is made based on responsive design technologies and is coded in PHP.
The overall UX to be similar to Tev Ulna - easy navigation, intuitive menus.

Industry/Entity Type

Property Management

Number of Pages Required

5+ page

Requirements
Must have
• Round dock buttons
Consistent icons across the application
Enough Spacing between buttons/icons/ menu
Consistent Font
Nice to have
• We would like the UX to allow the users to use the application without /minimum training.
Should not have
• we don't want anything that is classic with respect to UX

```html
<!DOCTYPE html>
<html lang="en">
<head>
<meta charset="utf-8">
<title>Estavo – Tenant List</title>
<link href="https://fonts.googleapis.com/css2?family=Inter:wght@400;500;600;700&display=swap" rel="stylesheet">
<style>
:root{
  --page-top:#ffffff;
  --page-bottom:#f3f7fc;
  --window:#f4f8fc;
  --panel:#ffffff;
  --tab:#dbeafb;
  --tab-active:#0d8bf5;
  --ink:#16202e;
  --muted:#7d8a99;
  --line:#e6ebf1;
  --head:#f6f8fb;
  --blue:#1a73e8;
  --cyan:#14a9f0;
  --green:#55c94a;
  --red:#f0524e;
  --active:#2ecc71;
  --orange:#f47c2b;
  --yellow:#f8c21c;
}
*{box-sizing:border-box;margin:0;padding:0}
html,body{width:1200px;height:1200px;overflow:hidden}
body{font-family:"Inter",sans-serif;color:var(--ink);background:linear-gradient(var(--page-top) 0 430px,var(--page-bottom) 430px);position:relative}
.window{position:absolute;left:84px;top:259px;width:1033px;height:740px;background:var(--window);border-radius:22px;box-shadow:0 10px 40px rgba(40,70,110,.06)}
.dots{position:absolute;left:32px;top:13px;display:flex;gap:6px}
.dots span{width:8px;height:8px;border-radius:50%}
.brand{position:absolute;left:32px;top:45px;display:flex;align-items:center;gap:6px;font-size:15px;font-weight:700;color:#1f8ef1}
.brand i{width:14px;height:14px;background:#1f8ef1;border-radius:3px}
.theme-toggle{position:absolute;left:741px;top:39px;width:62px;height:26px;border-radius:13px;background:#fff;border:1px solid #eef0f3;display:flex;align-items:center;justify-content:space-around}
.welcome{position:absolute;right:87px;top:44px;font-size:11.5px}
.welcome b{font-weight:600}
.avatar{position:absolute;left:959px;top:31px;width:40px;height:40px;border-radius:50%;background:linear-gradient(135deg,#6b4a3a,#2d2a2f)}
.page-title{position:absolute;left:38px;top:89px;display:flex;align-items:center;gap:11px;font-size:17px;font-weight:500}
.page-title .back{width:17px;height:17px;border-radius:50%;background:var(--ink);display:grid;place-items:center}
.tab{position:absolute;height:33px;border-radius:6px;background:var(--tab);font-size:9.5px;font-weight:500;display:grid;place-items:center}
.tab.active{background:var(--tab-active);color:#fff;font-weight:600;box-shadow:0 6px 12px rgba(13,139,245,.3)}
.panel{position:absolute;left:36px;top:226px;width:961px;height:324px;background:var(--panel);border-radius:10px}
.panel-head{height:48px;border-bottom:1px solid var(--line);display:flex;align-items:center;justify-content:space-between;padding:0 18px 0 19px}
.panel-head h2{font-size:13.5px;font-weight:600;display:flex;align-items:center;gap:8px}
.add-link{font-size:9.5px;font-weight:500;color:var(--ink);text-decoration:underline;display:flex;align-items:center;gap:5px}
.toolbar{height:44px;border-bottom:1px solid var(--line);position:relative;font-size:10.5px}
.toolbar .label{position:absolute;left:19px;top:14px;font-weight:500}
.search{position:absolute;left:70px;top:8px;width:163px;height:27px;border:1px solid #d3d9e0;border-radius:4px;padding:5px 10px}
.btn{position:absolute;top:8px;height:27px;border:1px solid #c9d0d8;border-radius:4px;font-size:9px;font-weight:500;display:flex;align-items:center;justify-content:center;gap:4px}
.show{position:absolute;left:810px;top:14px;font-size:9px;font-weight:600}
.select{position:absolute;left:843px;top:8px;width:63px;height:27px;border:1px solid #d3d9e0;border-radius:4px;font-size:9px;font-weight:600;padding:7px 13px}
.select::after{content:"";position:absolute;right:0;top:0;width:18px;height:25px;border-left:1px solid #d3d9e0}
.select .caret{position:absolute;right:6px;top:11px;border:3px solid transparent;border-top:4px solid var(--ink);z-index:1}
.entries{position:absolute;left:918px;top:14px;font-size:9px;color:var(--muted);font-weight:500}
.grid{display:grid;grid-template-columns:136px 148px 114px 106px 107px 121px 113px 116px}
.filters{height:43px;border-bottom:1px solid var(--line)}
.filters div{border-right:1px solid var(--line);padding:7px 6px 0 6px}
.filters div:last-child{border-right:0}
.filters span{display:block;height:26px;border:1px solid #d3d9e0;border-radius:4px;font-size:8.5px;color:var(--muted);padding:7px 10px}
.thead{height:33px;background:var(--head);font-size:9px;font-weight:600}
.thead div{display:flex;align-items:center;justify-content:space-between;padding:0 10px 0 12px;border-right:1px solid var(--line)}
.thead div:last-child{border-right:0}
.sort{display:flex;flex-direction:column;gap:2px}
.sort i{border:3px solid transparent;height:0}
.sort i:first-child{border-bottom:3px solid #b8c1cc;border-top:0}
.sort i:last-child{border-top:3px solid #b8c1cc;border-bottom:0}
.row{height:30px;border-bottom:1px solid var(--line);font-size:9px}
.row div{display:flex;align-items:center;padding:0 12px;border-right:1px solid var(--line)}
.row div:last-child{border-right:0;justify-content:center}
.actions{gap:8px;justify-content:center}
.act{width:18px;height:18px;border-radius:3px;display:grid;place-items:center}
.tenant-link{color:var(--blue);text-decoration:underline;font-weight:500}
.badge{width:59px;height:18px;border-radius:2px;background:var(--active);color:#fff;font-weight:600;display:grid;place-items:center}
.panel-foot{height:34px;position:relative;font-size:9px;font-weight:600}
.panel-foot .info{position:absolute;left:24px;top:12px}
.pager{position:absolute;right:37px;top:7px;display:flex;align-items:center;gap:16px}
.pager .num{width:18px;height:18px;background:#e6edf5;border-radius:3px;display:grid;place-items:center}
.pager .next{color:var(--muted);font-weight:500}
.dock{position:absolute;left:434px;top:599px;width:165px;height:65px;background:#fff;border-radius:12px;display:flex;align-items:center;justify-content:center;gap:35px}
.dock-btn{width:42px;height:42px;border-radius:11px;display:grid;place-items:center}
.dock-btn.home{background:linear-gradient(180deg,#1fa6ff,#0b78ee)}
.dock-btn.apps{background:linear-gradient(180deg,#ff8a3a,#f36a1f)}
</style>
</head>
<body>
<main class="window">
  <div class="dots"><span style="background:var(--yellow)"></span><span style="background:var(--red)"></span><span style="background:var(--active)"></span></div>
  <div class="brand"><i></i>Estavo</div>
  <div class="theme-toggle">
    <svg width="14" height="14" viewBox="0 0 14 14"><g stroke="#f5a623" stroke-width="1.4"><path d="M7 1v2M7 11v2M1 7h2M11 7h2M2.8 2.8l1.4 1.4M9.8 9.8l1.4 1.4M2.8 11.2l1.4-1.4M9.8 4.2l1.4-1.4"/></g><circle cx="7" cy="7" r="2.6" fill="#f8c21c"/></svg>
    <svg width="16" height="16" viewBox="0 0 16 16"><circle cx="8" cy="8" r="6.5" fill="#fff3c4" stroke="#f8c21c" stroke-width="2"/></svg>
  </div>
  <div class="welcome">Welcome, <b>Dana Rivers</b></div>
  <div class="avatar" role="img" aria-label="User profile photo"></div>
  <h1 class="page-title"><span class="back"><svg width="7" height="8" viewBox="0 0 7 8"><path d="M5 1L2 4l3 3" stroke="#fff" stroke-width="1.6" fill="none"/></svg></span>Crest Tower</h1>

  <nav>
    <div class="tab" style="left:39px;top:132px;width:130px">General information</div>
    <div class="tab" style="left:176px;top:132px;width:123px">Organization chart</div>
    <div class="tab active" style="left:308px;top:132px;width:97px">Tenant List</div>
    <div class="tab" style="left:412px;top:132px;width:108px">Property Assets</div>
    <div class="tab" style="left:526px;top:132px;width:108px">Contractor list</div>
    <div class="tab" style="left:641px;top:132px;width:131px">Compliance mngmt</div>
    <div class="tab" style="left:780px;top:132px;width:124px">Maint. Work orders</div>
    <div class="tab" style="left:912px;top:132px;width:93px">Work orders</div>
    <div class="tab" style="left:39px;top:177px;width:104px">Purchase orders</div>
    <div class="tab" style="left:151px;top:177px;width:61px">Files</div>
  </nav>

  <section class="panel">
    <header class="panel-head">
      <h2><svg width="15" height="15" viewBox="0 0 16 16"><circle cx="8" cy="8" r="7.5" fill="#16202e"/><circle cx="8" cy="6" r="2.6" fill="#fff"/><path d="M3.5 13a5 4 0 0 1 9 0" fill="#fff"/></svg>Tenant list</h2>
      <a class="add-link"><svg width="13" height="13" viewBox="0 0 14 14"><circle cx="7" cy="7" r="7" fill="#14a9f0"/><path d="M7 3.5v7M3.5 7h7" stroke="#fff" stroke-width="1.6"/></svg>Add a new tenant</a>
    </header>
    <div class="toolbar">
      <span class="label">Search</span>
      <div class="search"><svg width="13" height="13" viewBox="0 0 14 14"><circle cx="5.5" cy="5.5" r="4" stroke="#4a5564" stroke-width="1.8" fill="none"/><path d="M8.5 8.5L12.5 12.5" stroke="#4a5564" stroke-width="2"/></svg></div>
      <span class="btn" style="left:316px;width:63px">▢ Copy</span>
      <span class="btn" style="left:384px;width:63px">▯ Excel</span>
      <span class="btn" style="left:452px;width:63px">▯ CSV</span>
      <span class="btn" style="left:520px;width:63px">▯ PDF</span>
      <span class="btn" style="left:588px;width:73px">⎙ Print</span>
      <span class="show">Show</span>
      <div class="select">25<i class="caret"></i></div>
      <span class="entries">entries</span>
    </div>
    <div class="grid filters">
      <div></div>
      <div><span>Filter name</span></div>
      <div><span>Filter unit number</span></div>
      <div><span>Filter start date</span></div>
      <div><span>Filter end date</span></div>
      <div><span>Filter rented area</span></div>
      <div><span>Filter rented cost</span></div>
      <div></div>
    </div>
    <div class="grid thead">
      <div style="justify-content:center">Actions</div>
      <div>Tenant <svg width="7" height="5" viewBox="0 0 7 5"><path d="M0 5L3.5 0 7 5z" fill="#16202e"/></svg></div>
      <div>Unit number <span class="sort"><i></i><i></i></span></div>
      <div>Rent start date <span class="sort"><i></i><i></i></span></div>
      <div>Rent end date <span class="sort"><i></i><i></i></span></div>
      <div>Rented área (sq.ft.) <span class="sort"><i></i><i></i></span></div>
      <div>Price per sq.ft. <span class="sort"><i></i><i></i></span></div>
      <div><span style="margin-left:40px">Status</span> <span class="sort"><i></i><i></i></span></div>
    </div>
    <div class="rows">
      <!-- four identical tenant rows -->
      <div class="grid row"><div class="actions"><span class="act" style="background:var(--cyan)"><svg width="11" height="11" viewBox="0 0 12 12"><circle cx="5" cy="5" r="3.5" stroke="#fff" stroke-width="1.5" fill="none"/><path d="M7.5 7.5L11 11" stroke="#fff" stroke-width="1.6"/></svg></span><span class="act" style="background:var(--blue)"><svg width="11" height="11" viewBox="0 0 12 12"><path d="M2 3h4M2 3v7h7V6" stroke="#fff" stroke-width="1.3" fill="none"/><path d="M5 7l5-5" stroke="#fff" stroke-width="1.6"/></svg></span><span class="act" style="background:var(--green)"><svg width="11" height="11" viewBox="0 0 12 12"><path d="M2 2.5L4 1.5 5.5 4 4.3 5a6 6 0 0 0 2.7 2.7L8 6.5l2.5 1.5-1 2C5 10 2 7 2 2.5z" fill="#fff"/></svg></span><span class="act" style="background:var(--red)"><svg width="11" height="11" viewBox="0 0 12 12"><path d="M2 3h8M4.5 3V1.5h3V3M3 3l.6 7.5h4.8L9 3" stroke="#fff" stroke-width="1.3" fill="none"/></svg></span></div><div><span class="tenant-link">ORCHARD CO</span></div><div>100</div><div>04/01/2019</div><div>07/01/2022</div><div>12,500.00</div><div>12.00</div><div><span class="badge">Active</span></div></div>
      <div class="grid row"><div class="actions"><span class="act" style="background:var(--cyan)"><svg width="11" height="11" viewBox="0 0 12 12"><circle cx="5" cy="5" r="3.5" stroke="#fff" stroke-width="1.5" fill="none"/><path d="M7.5 7.5L11 11" stroke="#fff" stroke-width="1.6"/></svg></span><span class="act" style="background:var(--blue)"><svg width="11" height="11" viewBox="0 0 12 12"><path d="M2 3h4M2 3v7h7V6" stroke="#fff" stroke-width="1.3" fill="none"/><path d="M5 7l5-5" stroke="#fff" stroke-width="1.6"/></svg></span><span class="act" style="background:var(--green)"><svg width="11" height="11" viewBox="0 0 12 12"><path d="M2 2.5L4 1.5 5.5 4 4.3 5a6 6 0 0 0 2.7 2.7L8 6.5l2.5 1.5-1 2C5 10 2 7 2 2.5z" fill="#fff"/></svg></span><span class="act" style="background:var(--red)"><svg width="11" height="11" viewBox="0 0 12 12"><path d="M2 3h8M4.5 3V1.5h3V3M3 3l.6 7.5h4.8L9 3" stroke="#fff" stroke-width="1.3" fill="none"/></svg></span></div><div><span class="tenant-link">ORCHARD CO</span></div><div>100</div><div>04/01/2019</div><div>07/01/2022</div><div>12,500.00</div><div>12.00</div><div><span class="badge">Active</span></div></div>
      <div class="grid row"><div class="actions"><span class="act" style="background:var(--cyan)"><svg width="11" height="11" viewBox="0 0 12 12"><circle cx="5" cy="5" r="3.5" stroke="#fff" stroke-width="1.5" fill="none"/><path d="M7.5 7.5L11 11" stroke="#fff" stroke-width="1.6"/></svg></span><span class="act" style="background:var(--blue)"><svg width="11" height="11" viewBox="0 0 12 12"><path d="M2 3h4M2 3v7h7V6" stroke="#fff" stroke-width="1.3" fill="none"/><path d="M5 7l5-5" stroke="#fff" stroke-width="1.6"/></svg></span><span class="act" style="background:var(--green)"><svg width="11" height="11" viewBox="0 0 12 12"><path d="M2 2.5L4 1.5 5.5 4 4.3 5a6 6 0 0 0 2.7 2.7L8 6.5l2.5 1.5-1 2C5 10 2 7 2 2.5z" fill="#fff"/></svg></span><span class="act" style="background:var(--red)"><svg width="11" height="11" viewBox="0 0 12 12"><path d="M2 3h8M4.5 3V1.5h3V3M3 3l.6 7.5h4.8L9 3" stroke="#fff" stroke-width="1.3" fill="none"/></svg></span></div><div><span class="tenant-link">ORCHARD CO</span></div><div>100</div><div>04/01/2019</div><div>07/01/2022</div><div>12,500.00</div><div>12.00</div><div><span class="badge">Active</span></div></div>
      <div class="grid row"><div class="actions"><span class="act" style="background:var(--cyan)"><svg width="11" height="11" viewBox="0 0 12 12"><circle cx="5" cy="5" r="3.5" stroke="#fff" stroke-width="1.5" fill="none"/><path d="M7.5 7.5L11 11" stroke="#fff" stroke-width="1.6"/></svg></span><span class="act" style="background:var(--blue)"><svg width="11" height="11" viewBox="0 0 12 12"><path d="M2 3h4M2 3v7h7V6" stroke="#fff" stroke-width="1.3" fill="none"/><path d="M5 7l5-5" stroke="#fff" stroke-width="1.6"/></svg></span><span class="act" style="background:var(--green)"><svg width="11" height="11" viewBox="0 0 12 12"><path d="M2 2.5L4 1.5 5.5 4 4.3 5a6 6 0 0 0 2.7 2.7L8 6.5l2.5 1.5-1 2C5 10 2 7 2 2.5z" fill="#fff"/></svg></span><span class="act" style="background:var(--red)"><svg width="11" height="11" viewBox="0 0 12 12"><path d="M2 3h8M4.5 3V1.5h3V3M3 3l.6 7.5h4.8L9 3" stroke="#fff" stroke-width="1.3" fill="none"/></svg></span></div><div><span class="tenant-link">ORCHARD CO</span></div><div>100</div><div>04/01/2019</div><div>07/01/2022</div><div>12,500.00</div><div>12.00</div><div><span class="badge">Active</span></div></div>
    </div>
    <footer class="panel-foot">
      <span class="info">Showing 1 to 4 of 4 entries</span>
      <div class="pager"><span>Previous</span><span class="num">1</span><span class="next">Next</span></div>
    </footer>
  </section>

  <div class="dock">
    <span class="dock-btn home"><svg width="26" height="24" viewBox="0 0 26 24"><path d="M2 12L13 2l11 10" stroke="#fff" stroke-width="3" fill="none" stroke-linecap="round" stroke-linejoin="round"/><path d="M6 11v11h5v-6h4v6h5V11" fill="#fff"/></svg></span>
    <span class="dock-btn apps"><svg width="22" height="22" viewBox="0 0 22 22" fill="#fff"><circle cx="4" cy="4" r="2"/><circle cx="11" cy="4" r="2"/><circle cx="18" cy="4" r="2"/><circle cx="4" cy="11" r="2"/><circle cx="11" cy="11" r="2"/><circle cx="18" cy="11" r="2"/><circle cx="4" cy="18" r="2"/><circle cx="11" cy="18" r="2"/><circle cx="18" cy="18" r="2"/></svg></span>
  </div>
</main>
</body>
</html>
```